Brenvik Systems PowerPoint Template

Project Title: Professional & Functional PowerPoint Template (.potx) – Brenvik Systems Rebrand

Project Overview:
Brenvik Systems has recently undergone a complete rebranding, including a new logo, website, and visual identity. We need a professional, high-end PowerPoint Template (.potx) that reflects our new look while being highly functional for everyday use.

We previously had a design created, but it was built incorrectly (static images, oversized file, no Master Slides). The goal of this project is to take our new aesthetic and build a "workable" template where layouts are controlled by Master Slides and text is easily editable.

Style & Brand Direction:
The template must be an extension of our new website: https://www.brenvik-systems.example/

Aesthetic: Modern, clean, high-tech, and "Industrial Tech."

Color Palette: Please pull the primary blues, greys, and accent colors directly from the website.

Imagery/Graphics: Use clean lines and subtle tech-inspired gradients. Avoid "clutter."

Tone: Innovative, precise, and professional.

Technical Requirements (Crucial)
Format: Must be delivered as a PowerPoint Template file (** .potx **).

Functionality: All layouts must be built using Slide Masters. Users should be able to click "New Slide" and choose from specific layouts.

Native Elements: Do NOT use full-page background images for text areas. Bullet points must use native PowerPoint list functionality (not individual text boxes).

File Size: The template must be optimized and lightweight.

Fonts: Use standard professional fonts or provide the specific web-safe equivalent used on our site (e.g., Montserrat, Open Sans, etc.).

Required Slide Layouts
Please include a minimum of 10–12 Master layouts, including:
*Title Slide (2-3 variations: Dark and Light)
*Agenda/Table of Contents
*Section Header/Divider Slides
*Standard Text/Bullet Slide
*Two-Column Text Slide
*Image + Text Layouts (Left/Right variations)
*Data/Chart Slide (Styled bar/pie charts that match the brand)
*Process/Timeline Slide (Infographic style)
*Section slide

Attachments Provided
Brand Assets (.zip): Contains our new logo in various formats.

Inspiration/Existing PPT: We have attached the previous design created by our web agency. Note: Use this for visual inspiration ONLY. Do not copy the file structure, as it is technically flawed.

Deliverables
Final .potx file.

All used icons or custom graphics in vector format (if applicable).

Instruction note on any specific fonts used.

Target Market(s)

Internal communication and external (investors, customers)

Industry/Entity Type

Semiconductor, Automotive

Requirements
Must have
• A potx file

```html
<!DOCTYPE html>
<html lang="en">
<head>
<meta charset="utf-8">
<title>Brenvik Systems – Presentation Template Overview</title>
<link href="https://fonts.googleapis.com/css2?family=Inter+Tight:wght@300;400;500;700&display=swap" rel="stylesheet">
<style>
:root{
  --canvas:#b3b3b3;
  --white:#ffffff;
  --ink:#111216;
  --muted:#4a4d55;
  --line:#d5d8de;
  --panel:#f1f2f4;
  --brand:#2b55f5;
  --brand-deep:#1a3fd6;
  --navy:#0d2a5c;
  --cyan:#2fc3f0;
  --sky:#7cc6ee;
  --mid:#1f6fd1;
}
*{margin:0;padding:0;box-sizing:border-box}
html,body{width:859px;height:1200px;overflow:hidden}
body{background:var(--canvas);font-family:"Inter Tight",Arial,sans-serif;color:var(--ink);position:relative}
.slide{position:absolute;width:390px;height:219px;overflow:hidden;background:var(--white)}
.col-l{left:35px}.col-r{left:434px}
.row1{top:34px}.row2{top:263px}.row3{top:491px}.row4{top:720px}.row5{top:948px}
.abs{position:absolute}
.arrow-box{position:absolute;display:flex;align-items:center;justify-content:center}
.arrow-box svg{width:60%;height:60%}
.arrow-box.blue{background:var(--brand)}
.arrow-box.black{background:var(--ink)}
.mark-square{position:absolute;background:var(--brand)}
.wordmark{position:absolute;display:flex;align-items:center;gap:6px;font-weight:700;letter-spacing:.5px}
.wordmark .sq{background:var(--brand)}
.light{font-weight:300}
.item-title{font-size:10px;line-height:1.1;font-weight:400}
.item-body{font-size:7.2px;line-height:1.25;font-weight:300;color:var(--muted)}
.small{font-size:6.2px;line-height:1.3;font-weight:300}
.rule-left{border-left:.6px solid currentColor;padding-left:6px}
.placeholder{position:absolute}
.kicker{position:absolute;left:0;right:0;text-align:center;font-size:8px;letter-spacing:1.6px;font-weight:400}
.heading-c{position:absolute;left:0;right:0;text-align:center;font-size:22px;font-weight:400}
.card{position:absolute;padding:6px 7px}
.card.grey{background:var(--panel)}
.card.outlined{border:.6px solid #c9d2ea;background:var(--white)}
.card .item-title{margin-bottom:2px}
.tube{position:absolute;width:13px;height:96px;border-radius:7px;background:#e3e5e9;overflow:hidden;box-shadow:0 0 0 2px #f4f5f7}
.tube span{position:absolute;left:0;right:0;bottom:0}
.tube i{position:absolute;left:0;right:0;bottom:8px;font-style:normal;font-size:5px;color:#fff;writing-mode:vertical-rl;transform:rotate(180deg);text-align:center}
.bulb{position:absolute;width:21px;height:21px;border-radius:50%;background:#fff;box-shadow:0 1px 4px rgba(0,0,0,.2);display:flex;align-items:center;justify-content:center;font-size:10px;font-weight:500}
.label{position:absolute;width:70px}
.tl-dot{position:absolute;top:133px;width:7px;height:7px;border-radius:50%;border:.8px solid var(--brand);background:var(--ink)}
.tl-dot::after{content:"";position:absolute;left:1.4px;top:1.4px;width:2.6px;height:2.6px;border-radius:50%;background:var(--brand)}
.tl-item{position:absolute;width:70px;text-align:center;color:#fff}
.tl-item .item-body{color:#cfd3da}
.donut{position:absolute;width:28px;height:28px;border-radius:50%;background:#fff;box-shadow:0 1px 4px rgba(0,0,0,.25)}
.donut svg{width:100%;height:100%}
</style>
</head>
<body>

<!-- Title slide -->
<section class="slide col-l row1" aria-label="Title slide">
  <div class="placeholder" role="img" aria-label="Abstract blue and pink light-wave illustration" style="left:76px;top:27px;width:228px;height:114px;background:radial-gradient(ellipse at 65% 45%,rgba(43,85,245,.55),rgba(124,198,238,.25) 45%,rgba(240,170,220,.15) 65%,transparent 75%)"></div>
  <div class="wordmark" style="left:243px;top:25px;font-size:24px;color:var(--ink)"><span class="sq" style="width:23px;height:23px"></span>BRENVIK</div>
  <div class="arrow-box black" style="left:18px;top:108px;width:10px;height:10px"><svg viewBox="0 0 10 10"><path d="M2 8L8 2M3.5 2H8V6.5" stroke="#fff" fill="none" stroke-width="1.2"/></svg></div>
  <h1 class="abs light" style="left:30px;top:125px;font-size:25px;line-height:1.15;font-weight:400">Enlightened<br>Engineering</h1>
  <div class="arrow-box blue" style="left:206px;top:174px;width:20px;height:20px"><svg viewBox="0 0 10 10"><path d="M2 8L8 2M3.5 2H8V6.5" stroke="#fff" fill="none" stroke-width=".9"/></svg></div>
  <p class="abs light" style="left:242px;top:147px;width:130px;font-size:10.4px;line-height:1.2">Unlocking the power of light for cleaner, smarter, more scalable production.</p>
</section>

<!-- Agenda -->
<section class="slide col-r row1" aria-label="Agenda slide">
  <svg class="abs" style="left:0;top:0" width="390" height="219" viewBox="0 0 390 219">
    <path d="M0 68H250A31 41 0 0 1 281 109A31 41 0 0 1 250 150H0" fill="none" stroke="#d9dbe0" stroke-width=".7"/>
    <g fill="#fff" stroke="#d9dbe0" stroke-width=".7">
      <circle cx="45" cy="68" r="3"/><circle cx="123" cy="68" r="3"/><circle cx="204" cy="68" r="3"/>
      <circle cx="272" cy="85" r="3"/><circle cx="272" cy="133" r="3"/>
      <circle cx="45" cy="150" r="3"/><circle cx="123" cy="150" r="3"/><circle cx="204" cy="150" r="3"/>
    </g>
  </svg>
  <div class="abs" style="left:39px;top:31px"><div class="item-title">Lorem Ipsum</div><div class="item-body">Lorem ipsum dolor<br>sit amet</div></div>
  <div class="abs" style="left:117px;top:31px"><div class="item-title">Lorem Ipsum</div><div class="item-body">Lorem ipsum dolor<br>sit amet</div></div>
  <div class="abs" style="left:198px;top:31px"><div class="item-title">Lorem Ipsum</div><div class="item-body">Lorem ipsum dolor<br>sit amet</div></div>
  <div class="abs" style="left:287px;top:64px"><div class="item-title">Lorem Ipsum</div><div class="item-body">Lorem ipsum dolor<br>sit amet</div></div>
  <div class="abs" style="left:287px;top:113px"><div class="item-title">Lorem Ipsum</div><div class="item-body">Lorem ipsum dolor<br>sit amet</div></div>
  <div class="abs" style="left:39px;top:164px"><div class="item-title">Lorem Ipsum</div><div class="item-body">Lorem ipsum dolor<br>sit amet</div></div>
  <div class="abs" style="left:117px;top:164px"><div class="item-title">Lorem Ipsum</div><div class="item-body">Lorem ipsum dolor<br>sit amet</div></div>
  <div class="abs" style="left:198px;top:164px"><div class="item-title">Lorem Ipsum</div><div class="item-body">Lorem ipsum dolor<br>sit amet</div></div>
  <h2 class="abs" style="left:169px;top:92px;font-size:25px;font-weight:400">Agenda</h2>
  <div class="arrow-box black" style="left:146px;top:118px;width:19px;height:19px"><svg viewBox="0 0 10 10"><path d="M2 8L8 2M3.5 2H8V6.5" stroke="#fff" fill="none" stroke-width="1"/></svg></div>
</section>

<!-- Image + text -->
<section class="slide col-l row2" aria-label="Image and text slide">
  <p class="abs" style="left:25px;top:57px;width:145px;font-size:11.4px;line-height:1.23">For industries driving tech forward, Brenvik is the most advanced laser-based manufacturing partner</p>
  <p class="abs small rule-left" style="left:25px;top:124px;width:148px;color:var(--muted)">Lorem ipsum dolor sit amet, consectetur adipiscing elit, sed do eiusmod tempor incididunt ut labore et dolore magna aliqua. Quis ipsum suspendisse ultrices gravida. Risus commodo viverra maecenas accumsan lacus vel facilisis.</p>
  <div class="placeholder" role="img" aria-label="Photo of a laser cutting head throwing sparks" style="left:181px;top:9px;width:200px;height:202px;background:radial-gradient(circle at 75% 45%,#d98a2a 0%,#6b4a2c 25%,#2b2b2e 60%,#1b1c20 100%)"></div>
  <ul class="abs small" style="left:198px;top:124px;width:150px;color:#fff;list-style:none">
    <li style="margin-bottom:3px">↗&nbsp; Lorem ipsum dolor sit amet, consectetur adipiscing elit, sed do eiusmod tempor incididunt ut labore et dolore magna aliqua</li>
    <li style="margin-bottom:3px">↗&nbsp; Quis ipsum suspendisse ultrices gravida.</li>
    <li>↗&nbsp; Risus commodo viverra maecenas accumsan lacus vel facilisis.</li>
  </ul>
  <div class="mark-square" style="left:353px;top:182px;width:19px;height:19px"></div>
  <div class="arrow-box blue" style="left:172px;top:27px;width:15px;height:15px"><svg viewBox="0 0 10 10"><path d="M2 8L8 2M3.5 2H8V6.5" stroke="#fff" fill="none" stroke-width="1"/></svg></div>
</section>

<!-- Section divider -->
<section class="slide col-r row2" aria-label="Section divider slide">
  <div class="abs" style="left:0;top:0;width:390px;height:105px;background:var(--brand)"></div>
  <h2 class="abs" style="left:30px;top:42px;font-size:21px;line-height:1.05;font-weight:400;color:#fff">Section<br>Divider</h2>
  <div class="arrow-box black" style="left:104px;top:32px;width:15px;height:15px"><svg viewBox="0 0 10 10"><path d="M2 8L8 2M3.5 2H8V6.5" stroke="#fff" fill="none" stroke-width="1"/></svg></div>
  <p class="abs small rule-left" style="left:214px;top:60px;width:150px;color:#fff">Lorem ipsum dolor sit amet, consectetur adipiscing elit, sed do eiusmod tempor incididunt ut labore et dolore magna aliqua.</p>
  <p class="abs small" style="left:29px;top:126px;width:142px;color:var(--muted)">Lorem ipsum dolor sit amet, consectetur adipiscing elit, sed do eiusmod tempor incididunt ut labore et dolore magna aliqua. Quis ipsum suspendisse ultrices gravida. Risus commodo viverra maecenas accumsan lacus vel facilisis.</p>
  <p class="abs small" style="left:29px;top:171px;width:142px;color:var(--ink)">Lorem ipsum dolor sit amet, consectetur adipiscing elit, sed do eiusmod tempor.</p>
  <div class="placeholder" role="img" aria-label="Photo of a rocket engine in an industrial hall" style="left:181px;top:114px;width:200px;height:96px;background:linear-gradient(120deg,#1f2a38,#5a5650 45%,#8a6a40 70%,#2a2f38)"></div>
</section>

<!-- Benefits -->
<section class="slide col-l row3" aria-label="Benefits slide">
  <div class="mark-square" style="left:362px;top:7px;width:20px;height:20px;background:#c9cbd0"></div>
  <h2 class="abs" style="left:27px;top:57px;font-size:21px;line-height:1.05;font-weight:400">Partner with<br>Precision</h2>
  <div class="arrow-box blue" style="left:125px;top:94px;width:10px;height:10px"><svg viewBox="0 0 10 10"><path d="M2 8L8 2M3.5 2H8V6.5" stroke="#fff" fill="none" stroke-width="1.2"/></svg></div>
  <p class="abs small" style="left:28px;top:111px;width:118px;color:var(--muted)">Lorem ipsum dolor sit amet, consectetur adipiscing elit, sed do eiusmod tempor incididunt ut labore et dolore magna.</p>
  <p class="abs small" style="left:28px;top:145px;width:118px;color:var(--muted)">Quis ipsum suspendisse ultrices gravida. Risus commodo viverra maecenas accumsan lacus vel facilisis.</p>
  <div class="card grey" style="left:162px;top:38px;width:100px;height:53px"><div class="item-title">Minimize Cost</div><div class="item-body">Eliminate expensive tools while reducing labor costs through full automation.</div></div>
  <div class="card outlined" style="left:162px;top:96px;width:100px;height:73px"><div class="item-title">Improve Quality</div><div class="item-body">Laser-controlled geometry creates ultra-smooth surfaces that enhance device performance</div></div>
  <div class="arrow-box black" style="left:226px;top:163px;width:18px;height:18px"><svg viewBox="0 0 10 10"><path d="M2 8L8 2M3.5 2H8V6.5" stroke="#fff" fill="none" stroke-width="1"/></svg></div>
  <div class="card outlined" style="left:266px;top:56px;width:100px;height:53px"><div class="item-title">Reduce Waste</div><div class="item-body">Achieve 2.2–2.3 wafers per mm with 90% kerf loss reduction</div></div>
  <div class="arrow-box blue" style="left:343px;top:49px;width:9px;height:9px"><svg viewBox="0 0 10 10"><path d="M2 8L8 2M3.5 2H8V6.5" stroke="#fff" fill="none" stroke-width="1.3"/></svg></div>
  <div class="card grey" style="left:266px;top:114px;width:100px;height:60px"><div class="item-title">Increase Yields</div><div class="item-body">Consistent process prevents stress damage while delivering predictable output</div></div>
</section>

<!-- Bar chart -->
<section class="slide col-r row3" aria-label="Bar chart slide">
  <div class="kicker" style="top:27px">LOREM IPSUM</div>
  <div class="heading-c" style="top:36px">Lorem Ipsum</div>
  <div class="tube" style="left:134px;top:80px"><span style="height:40%;background:var(--sky)"></span><i>40%</i></div>
  <div class="tube" style="left:166px;top:80px"><span style="height:52%;background:#2a8fd8"></span><i>52%</i></div>
  <div class="tube" style="left:199px;top:80px"><span style="height:70%;background:#2a5fb8"></span><i>70%</i></div>
  <div class="tube" style="left:231px;top:80px"><span style="height:85%;background:#1c2f5c"></span><i>85%</i></div>
  <div class="bulb" style="left:130px;top:164px;color:var(--sky)">A</div>
  <div class="bulb" style="left:162px;top:164px;color:#2a8fd8">B</div>
  <div class="bulb" style="left:195px;top:164px;color:#2a5fb8">C</div>
  <div class="bulb" style="left:227px;top:164px;color:#1c2f5c">D</div>
  <div class="label" style="left:52px;top:78px"><div class="item-title">Lorem Ipsum</div><div class="item-body">Lorem ipsum dolor sit amet</div></div>
  <div class="label" style="left:37px;top:117px"><div class="item-title">Lorem Ipsum</div><div class="item-body">Lorem ipsum dolor sit amet</div></div>
  <div class="label" style="left:52px;top:161px"><div class="item-title">Lorem Ipsum</div><div class="item-body">Lorem ipsum dolor sit amet</div></div>
  <div class="label" style="left:278px;top:78px"><div class="item-title">Lorem Ipsum</div><div class="item-body">Lorem ipsum dolor sit amet</div></div>
  <div class="label" style="left:299px;top:117px"><div class="item-title">Lorem Ipsum</div><div class="item-body">Lorem ipsum dolor sit amet</div></div>
  <div class="label" style="left:278px;top:161px"><div class="item-title">Lorem Ipsum</div><div class="item-body">Lorem ipsum dolor sit amet</div></div>
</section>

<!-- Timeline -->
<section class="slide col-l row4" aria-label="Timeline slide" style="background:var(--ink)">
  <div class="arrow-box" style="left:31px;top:37px;width:14px;height:14px"><svg viewBox="0 0 10 10"><path d="M2 8L8 2M3.5 2H8V6.5" stroke="#fff" fill="none" stroke-width="1"/></svg></div>
  <div class="abs" style="left:58px;top:27px;font-size:10px;letter-spacing:2px;color:#fff">LOREM IPSUM</div>
  <div class="abs" style="left:58px;top:38px;font-size:18px;color:#fff">Lorem Ipsum</div>
  <p class="abs small rule-left" style="left:185px;top:33px;width:150px;color:#fff">Lorem ipsum dolor sit amet, consectetur adipiscing elit, sed do eiusmod tempor incididunt ut labore et dolore magna aliqua.</p>
  <div class="arrow-box blue" style="left:348px;top:30px;width:9px;height:9px"><svg viewBox="0 0 10 10"><path d="M2 8L8 2M3.5 2H8V6.5" stroke="#fff" fill="none" stroke-width="1.3"/></svg></div>
  <div class="abs" style="left:0;top:136px;width:390px;height:.7px;background:#d8dbe2"></div>
  <div class="tl-dot" style="left:66px"></div><div class="tl-dot" style="left:114px"></div><div class="tl-dot" style="left:166px"></div>
  <div class="tl-dot" style="left:217px"></div><div class="tl-dot" style="left:267px"></div><div class="tl-dot" style="left:318px"></div>
  <div class="tl-item" style="left:34px;top:84px"><div class="item-title">Lorem Ipsum</div><div class="item-body">Lorem ipsum dolor sit amet, consectetur adipiscing elit</div></div>
  <div class="tl-item" style="left:134px;top:84px"><div class="item-title">Lorem Ipsum</div><div class="item-body">Lorem ipsum dolor sit amet, consectetur adipiscing elit</div></div>
  <div class="tl-item" style="left:235px;top:84px"><div class="item-title">Lorem Ipsum</div><div class="item-body">Lorem ipsum dolor sit amet, consectetur adipiscing elit</div></div>
  <div class="tl-item" style="left:82px;top:150px"><div class="item-title">Lorem Ipsum</div><div class="item-body">Lorem ipsum dolor sit amet, consectetur adipiscing elit</div></div>
  <div class="tl-item" style="left:185px;top:150px"><div class="item-title">Lorem Ipsum</div><div class="item-body">Lorem ipsum dolor sit amet, consectetur adipiscing elit</div></div>
  <div class="tl-item" style="left:286px;top:150px"><div class="item-title">Lorem Ipsum</div><div class="item-body">Lorem ipsum dolor sit amet, consectetur adipiscing elit</div></div>
  <div class="mark-square" style="left:11px;top:191px;width:18px;height:18px"></div>
</section>

<!-- Pie / donut data -->
<section class="slide col-r row4" aria-label="Data slide with donut and pie charts">
  <div class="kicker" style="top:22px;left:0;right:0">LOREM IPSUM</div>
  <div class="heading-c" style="top:30px">Lorem Ipsum</div>
  <div class="card grey" style="left:28px;top:59px;width:77px;height:53px"><div style="padding:14px 0 0 14px"><div class="item-title" style="font-size:8.5px">Lorem Ipsum</div><div class="item-body" style="font-size:6.5px">Lorem ipsum<br>dolor sit amet</div></div></div>
  <div class="card outlined" style="left:28px;top:120px;width:77px;height:53px"><div style="padding:3px 0 0 14px"><div class="item-title" style="font-size:8.5px">Lorem Ipsum</div><div class="item-body" style="font-size:6.5px">Lorem ipsum<br>dolor sit amet</div></div></div>
  <div class="card outlined" style="left:112px;top:79px;width:77px;height:53px"><div style="padding:17px 0 0 0"><div class="item-title" style="font-size:8.5px">Lorem Ipsum</div><div class="item-body" style="font-size:6.5px">Lorem ipsum<br>dolor sit amet</div></div></div>
  <div class="card grey" style="left:112px;top:139px;width:77px;height:53px"><div style="padding:4px 0 0 0"><div class="item-title" style="font-size:8.5px">Lorem Ipsum</div><div class="item-body" style="font-size:6.5px">Lorem ipsum<br>dolor sit amet</div></div></div>
  <div class="donut" style="left:19px;top:46px"><svg viewBox="0 0 28 28"><circle cx="14" cy="14" r="9" fill="none" stroke="#e7e9ee" stroke-width="3"/><circle cx="14" cy="14" r="9" fill="none" stroke="var(--navy)" stroke-width="3" stroke-dasharray="28.3 56.5" transform="rotate(90 14 14)"/><text x="14" y="15.5" font-size="4.5" text-anchor="middle" fill="var(--brand)" font-weight="700">50%</text></svg></div>
  <div class="donut" style="left:21px;top:156px"><svg viewBox="0 0 28 28"><circle cx="14" cy="14" r="9" fill="none" stroke="#e7e9ee" stroke-width="3"/><circle cx="14" cy="14" r="9" fill="none" stroke="var(--cyan)" stroke-width="3" stroke-dasharray="26.6 56.5" transform="rotate(90 14 14)"/><text x="14" y="15.5" font-size="4.5" text-anchor="middle" fill="var(--navy)" font-weight="700">47%</text></svg></div>
  <div class="donut" style="left:172px;top:70px"><svg viewBox="0 0 28 28"><circle cx="14" cy="14" r="9" fill="none" stroke="#e7e9ee" stroke-width="3"/><circle cx="14" cy="14" r="9" fill="none" stroke="var(--cyan)" stroke-width="3" stroke-dasharray="26.6 56.5" transform="rotate(90 14 14)"/><text x="14" y="15.5" font-size="4.5" text-anchor="middle" fill="var(--navy)" font-weight="700">47%</text></svg></div>
  <div class="donut" style="left:172px;top:176px"><svg viewBox="0 0 28 28"><circle cx="14" cy="14" r="9" fill="none" stroke="#e7e9ee" stroke-width="3"/><circle cx="14" cy="14" r="9" fill="none" stroke="var(--navy)" stroke-width="3" stroke-dasharray="42.4 56.5" transform="rotate(90 14 14)"/><text x="14" y="15.5" font-size="4.5" text-anchor="middle" fill="var(--brand)" font-weight="700">75%</text></svg></div>
  <svg class="abs" style="left:0;top:0" width="390" height="219" viewBox="0 0 390 219">
    <path d="M368 113L358.9 61.8A52 52 0 0 1 385.8 64.1Z" fill="var(--navy)"/>
    <path d="M368 113L330.4 99.3A40 40 0 0 1 361.1 73.6Z" fill="var(--cyan)"/>
    <path d="M368 113L337.9 123.9A32 32 0 0 1 337.9 102.1Z" fill="var(--mid)"/>
    <path d="M368 113L352.5 135.1A27 27 0 0 1 342.6 122.2Z" fill="var(--navy)"/>
    <path d="M368 113L394 158A52 52 0 0 1 338.2 155.6Z" fill="var(--cyan)"/>
    <path d="M368 113L385.8 64.1A52 52 0 0 1 420 113Z" fill="var(--mid)"/>
    <circle cx="368" cy="113" r="12" fill="#fff"/>
    <circle cx="368" cy="113" r="9" fill="var(--navy)"/>
  </svg>
  <div class="label" style="left:307px;top:23px"><div class="item-title" style="font-size:8.5px">Lorem Ipsum</div><div class="item-body" style="font-size:6.5px">Lorem ipsum<br>dolor sit amet</div></div>
  <div class="label" style="left:271px;top:59px"><div class="item-title" style="font-size:8.5px">Lorem Ipsum</div><div class="item-body" style="font-size:6.5px">Lorem ipsum<br>dolor sit amet</div></div>
  <div class="label" style="left:253px;top:100px"><div class="item-title" style="font-size:8.5px">Lorem Ipsum</div><div class="item-body" style="font-size:6.5px">Lorem ipsum<br>dolor sit amet</div></div>
  <div class="label" style="left:276px;top:139px"><div class="item-title" style="font-size:8.5px">Lorem Ipsum</div><div class="item-body" style="font-size:6.5px">Lorem ipsum<br>dolor sit amet</div></div>
  <div class="label" style="left:297px;top:180px"><div class="item-title" style="font-size:8.5px">Lorem Ipsum</div><div class="item-body" style="font-size:6.5px">Lorem ipsum<br>dolor sit amet</div></div>
</section>

<!-- Break slide -->
<section class="slide col-l row5" aria-label="Break slide" style="background:linear-gradient(135deg,#2a5df8,#1e45e8 60%,#3d6cff)">
  <div class="placeholder" role="img" aria-label="Line drawing of a laser processing machine" style="left:52px;top:21px;width:111px;height:176px;background:rgba(255,255,255,.1)"></div>
  <h2 class="abs" style="left:189px;top:88px;font-size:23px;font-weight:500;color:#fff">Break Slide</h2>
  <p class="abs small rule-left" style="left:189px;top:120px;width:150px;color:#fff">Lorem ipsum dolor sit amet, consectetur adipiscing elit, sed do eiusmod tempor incididunt ut labore et dolore magna aliqua.</p>
</section>

<!-- Closing -->
<section class="slide col-r row5" aria-label="Closing slide" style="background:radial-gradient(ellipse at 50% 65%,#1840c8,#0a1a5a 55%,#05081c 100%)">
  <div class="wordmark" style="left:129px;top:37px;font-size:25px;color:#fff"><span class="sq" style="width:26px;height:26px;background:#fff"></span>BRENVIK</div>
  <div class="placeholder" role="img" aria-label="Hand-lettered thank you message" style="left:132px;top:97px;width:127px;height:37px;background:rgba(255,255,255,.14)"></div>
  <div class="abs" style="left:150px;top:159px;display:flex;align-items:center;gap:6px;font-size:8px;color:#fff">
    <svg width="7" height="8" viewBox="0 0 7 8"><path d="M0 0L6 4.5L3.4 4.8L4.8 7.6L3.9 8L2.5 5.2L0.6 6.8Z" fill="#fff"/></svg>
    brenvik-systems.example
  </div>
</section>

</body>
</html>
```